Oven Cleaning flyer design

Hi there,
I need help designing a letterbox flyer. It needs to be DL size.
I have attached a rough design made with Chat GPT.
Would like back and front, have my business colors.
Please find attached mock up of what I would roughly like.
Also find attached logo.
Thank you

Target Market(s)

Home owners over 40

Industry/Entity Type

Cleaning

Requirements
Must have
• Logo, before after of oven, brand colors

```html
<!DOCTYPE html>
<html lang="en">
<head>
<meta charset="utf-8">
<title>Glow Oven Care – DL Flyer</title>
<link href="https://fonts.googleapis.com/css2?family=Krona+One&family=Roboto+Condensed:wght@400;700&family=Anton&display=swap" rel="stylesheet">
<style>
  :root{
    --teal:#47c1c8;
    --teal-dark:#2a7f86;
    --ink:#000;
    --paper:#fff;
    --stage:#888;
    --head:"Krona One",sans-serif;
    --body:"Roboto Condensed",sans-serif;
    --display:"Anton",sans-serif;
  }
  *{box-sizing:border-box;margin:0;padding:0}
  html,body{width:1178px;height:1200px;overflow:hidden;background:var(--stage)}
  .canvas{position:relative;width:1178px;height:1200px}
  .flyer{position:absolute;top:174px;width:414px;height:851px;overflow:hidden}
  .flyer--front{left:162px;background:var(--paper)}
  .flyer--back{left:602px;background:var(--ink)}
  .abs{position:absolute}
  .center{left:0;right:0;text-align:center;white-space:nowrap}

  .brand{position:absolute;left:0;right:0;display:flex;align-items:center;justify-content:center;gap:14px}
  .brand__dot{width:62px;height:62px;border-radius:50%;background:var(--teal)}
  .brand__name{font-family:var(--head);font-size:20px;line-height:1.25;color:var(--teal);text-align:left}
  .flyer--front .brand{top:28px}
  .flyer--back .brand{top:38px}

  .headline{font-family:var(--head);font-size:23px;line-height:32px;color:var(--ink);font-weight:400}
  .headline em{font-style:normal;color:var(--teal)}
  .rule-dots{left:0;right:0;top:186px;border-top:1px dotted #cfd8d9}
  .rule-bar{top:186px;left:178px;width:58px;height:3px;background:var(--teal)}
  .lede{top:204px;padding:0 20px;white-space:normal;font-family:var(--body);font-size:17px;line-height:21px;color:#111}

  .front-dark{left:0;right:0;top:427px;bottom:0;background:var(--ink)}
  .ring{left:42px;top:283px;width:316px;height:316px;border-radius:50%;border:14px solid var(--teal);border-bottom-color:transparent;transform:rotate(-20deg)}
  .photo-main{left:68px;top:310px;width:266px;height:266px;border-radius:50%;overflow:hidden;background:linear-gradient(90deg,#b06a22 0%,#6b3b12 48%,#2b2b2b 52%,#5d6164 100%)}
  .split-labels{left:0;right:0;top:0;height:48px;display:flex;background:var(--teal-dark)}
  .split-labels span{flex:1;padding-top:22px;font-family:var(--head);font-size:9.5px;color:#fff}
  .split-labels span:first-child{text-align:right;padding-right:12px;border-right:1px solid #fff}
  .split-labels span:last-child{text-align:left;padding-left:14px}
  .photo-small{left:177px;top:500px;width:176px;height:176px;border-radius:50%;border:7px solid #fff;overflow:hidden;background:linear-gradient(90deg,#3a2a1c 0%,#5a3d22 49%,#8d9092 51%,#c5c9cc 100%)}
  .mini-labels{left:28px;right:28px;top:76px;height:12px;display:flex;background:var(--teal-dark)}
  .mini-labels span{flex:1;text-align:center;font-family:var(--head);font-size:5px;line-height:12px;color:#fff}

  .call{top:704px;font-family:var(--head);font-size:25px;color:var(--teal)}
  .call-sub{top:738px;font-family:var(--body);font-weight:700;font-size:28px;color:#fff}
  .phone{display:flex;align-items:center;justify-content:center;gap:10px;font-family:var(--head);color:var(--teal)}
  .flyer--front .phone{top:778px;font-size:25px}
  .web-bar{left:0;right:0;bottom:0;height:37px;background:var(--teal);font-family:var(--body);font-weight:700;font-size:25px;line-height:37px;color:#fff}
  .web-bar b{color:var(--ink);font-weight:700}

  .why{top:142px;font-family:var(--head);font-size:17px;line-height:24px;color:#fff}
  .why em{font-style:normal;color:var(--teal)}
  .why-rule{top:196px;left:179px;width:57px;height:3px;background:#fff}
  .about{top:212px;padding:0 38px;white-space:normal;font-family:var(--body);font-weight:700;font-size:12px;line-height:19.5px;color:#fff}
  .mention{top:308px;font-family:var(--head);font-size:14px;color:var(--teal)}
  .offer{left:57px;top:331px;width:300px;height:109px;border-radius:14px;background:var(--paper);text-align:center}
  .offer__amount{font-family:var(--display);font-size:60px;line-height:74px;color:var(--teal);padding-top:4px}
  .offer__note{font-family:var(--head);font-size:14.5px;color:var(--ink);white-space:nowrap}
  .back-teal{left:0;right:0;top:522px;height:273px;background:var(--teal)}
  .features{left:0;right:0;top:474px;display:flex;justify-content:space-around;padding:0 8px}
  .feature{width:128px;text-align:center}
  .feature__icon{width:86px;height:86px;margin:0 auto;border-radius:50%;background:var(--ink);border:4px solid #fff;display:flex;align-items:center;justify-content:center}
  .feature__label{margin-top:18px;font-family:var(--head);font-size:9.5px;line-height:15px;color:var(--ink);white-space:nowrap}
  .also{left:35px;top:629px;width:343px;height:79px;border-radius:14px;background:var(--paper);text-align:center;box-shadow:0 10px 10px -6px rgba(0,0,0,.45)}
  .also__title{font-family:var(--head);font-size:21px;line-height:40px;color:var(--ink);padding-top:4px;white-space:nowrap}
  .also__list{font-family:var(--body);font-weight:700;font-size:24px;line-height:28px;color:var(--teal);white-space:nowrap}
  .flyer--back .phone{top:740px;font-size:29px;color:#fff}
  .web-black{left:0;right:0;top:795px;height:56px;font-family:var(--body);font-weight:700;font-size:26px;line-height:56px;color:#fff}
  .web-black b{color:var(--teal);font-weight:700}
</style>
</head>
<body>
<div class="canvas">

  <section class="flyer flyer--front">
    <div class="brand">
      <span class="brand__dot"></span>
      <span class="brand__name">GLOW OVEN<br>CARE</span>
    </div>
    <h1 class="abs center headline" style="top:120px">BRING YOUR <em>OVEN</em><br>BACK TO LIFE</h1>
    <div class="abs rule-dots"></div>
    <div class="abs rule-bar"></div>
    <p class="abs center lede">Professional, non-caustic oven cleaning that removes built-up grease, smoke, and burnt grime - leaving your oven looking fresh again.</p>

    <div class="abs front-dark"></div>
    <div class="abs ring"></div>
    <div class="abs photo-main" role="img" aria-label="Oven interior photo split in two: greasy before, clean after">
      <div class="abs split-labels"><span>BEFORE</span><span>AFTER</span></div>
    </div>
    <div class="abs photo-small" role="img" aria-label="Close-up oven photo split: dirty before, shiny after">
      <div class="abs mini-labels"><span>BEFORE</span><span>AFTER</span></div>
    </div>

    <p class="abs center call">CALL NOW FOR</p>
    <p class="abs center call-sub">Fast, Professional Service</p>
    <p class="abs center phone">
      <svg width="22" height="22" viewBox="0 0 24 24" aria-hidden="true"><path d="M6.6 10.8a15 15 0 0 0 6.6 6.6l2.2-2.2c.3-.3.7-.4 1-.2 1.1.4 2.3.6 3.6.6.6 0 1 .4 1 1V20c0 .6-.4 1-1 1A17 17 0 0 1 3 4c0-.6.4-1 1-1h3.5c.6 0 1 .4 1 1 0 1.3.2 2.5.6 3.6.1.3 0 .7-.2 1z" fill="#fff"/></svg>
      0412 555 019
    </p>
    <p class="abs center web-bar">www.<b>glowovencare</b>.com.au</p>
  </section>

  <section class="flyer flyer--back">
    <div class="brand">
      <span class="brand__dot"></span>
      <span class="brand__name">GLOW OVEN<br>CARE</span>
    </div>
    <h2 class="abs center why">WHY CHOOSE GLOW<br><em>OVEN CARE?</em></h2>
    <div class="abs why-rule"></div>
    <p class="abs center about">We're a local family business providing professional, non-caustic oven cleaning across Sunshine Coast. Using specialized-equipment and proven cleaning methods, we remove heavy grease, carbon build-up, smoke residue, restoring your oven safely and effectively.</p>
    <p class="abs center mention">MENTION THIS FLYER FOR</p>
    <div class="abs offer">
      <p class="offer__amount">$10 OFF</p>
      <p class="offer__note">YOUR FIRST CLEAN</p>
    </div>

    <div class="abs back-teal"></div>
    <div class="abs features">
      <div class="feature">
        <div class="feature__icon">
          <svg width="42" height="42" viewBox="0 0 42 42" aria-hidden="true"><circle cx="24" cy="16" r="9" fill="none" stroke="#47c1c8" stroke-width="3"/><path d="M20 16l3 3 5-6" fill="none" stroke="#47c1c8" stroke-width="2.5"/><path d="M4 32h10l8 3 14-7" fill="none" stroke="#47c1c8" stroke-width="3" stroke-linecap="round"/></svg>
        </div>
        <p class="feature__label">Reliable<br>Service</p>
      </div>
      <div class="feature">
        <div class="feature__icon">
          <svg width="42" height="42" viewBox="0 0 42 42" aria-hidden="true"><rect x="5" y="8" width="32" height="24" rx="2" fill="none" stroke="#47c1c8" stroke-width="3"/><rect x="9" y="12" width="18" height="16" fill="#47c1c8"/><circle cx="32" cy="16" r="1.8" fill="#47c1c8"/><circle cx="32" cy="23" r="1.8" fill="#47c1c8"/></svg>
        </div>
        <p class="feature__label">Non-Caustic<br>Cleaning</p>
      </div>
      <div class="feature">
        <div class="feature__icon">
          <svg width="42" height="42" viewBox="0 0 42 42" aria-hidden="true"><circle cx="21" cy="17" r="12" fill="#47c1c8"/><path d="M15 17l4 4 8-8" fill="none" stroke="#000" stroke-width="3"/><path d="M14 27l-3 10 5-2 3 4 2-9M28 27l3 10-5-2-3 4-2-9" fill="#47c1c8"/></svg>
        </div>
        <p class="feature__label">Satisfaction<br>Guaranteed</p>
      </div>
    </div>

    <div class="abs also">
      <p class="also__title">WE ALSO CLEAN</p>
      <p class="also__list">Cooktops, Rangehoods and BBQs</p>
    </div>
    <p class="abs center phone">
      <svg width="24" height="24" viewBox="0 0 24 24" aria-hidden="true"><path d="M6.6 10.8a15 15 0 0 0 6.6 6.6l2.2-2.2c.3-.3.7-.4 1-.2 1.1.4 2.3.6 3.6.6.6 0 1 .4 1 1V20c0 .6-.4 1-1 1A17 17 0 0 1 3 4c0-.6.4-1 1-1h3.5c.6 0 1 .4 1 1 0 1.3.2 2.5.6 3.6.1.3 0 .7-.2 1z" fill="#fff"/></svg>
      0412 555 019
    </p>
    <p class="abs center web-black">www.<b>glowovencare</b>.com.au</p>
  </section>

</div>
</body>
</html>
```